Business card for Sports Apparel business

DOUBLE SIDED DESIGN
We need business cards for a new sports apparel business. We are developing a protective headband for soccer initially.
Torvalle is focused on designing and developing head protection products to reduce the likelihood of concussion when playing sports. Exploring and understanding medical insights, material science research, current and former players experiences and governing bodies guidelines has allowed Torvalle to develop the safety, style, form and function requirements of a suitable product to bring to market.
Target Market(s)
Mums buying kits for the sons and daughters. Amateur footballers.
Industry/Entity Type
Sporting Good
Contact Information for Business Card
Martin Ashworth - CEO
Mobile: +44 7431589027
Email: martin@torvalle.co.uk
Tel: 0208 5519372
Helena Pargeter - COO
Mob: +44 7385 640117
Email: helena@torvalle.co.uk
Tel: 0208 5519372
Duncan Farrow - CCO
Mob: +44 7564 293081
Email: duncan@torvalle.co.uk
Tel: 0208 5519372
Look and feel
Each slider illustrates characteristics of the customer's brand and the style your logo design should communicate.

```html
<!DOCTYPE html>
<html lang="en">
<head>
<meta charset="utf-8">
<title>Torvalle Business Card</title>
<link href="https://fonts.googleapis.com/css2?family=Lato:wght@400;700;900&display=swap" rel="stylesheet">
<style>
  :root {
    --brand-blue: #17609a;
    --ink-grey: #4a4a4a;
    --paper: #ffffff;
    --backdrop: #e9ebee;
  }
  * { margin: 0; padding: 0; box-sizing: border-box; }
  html, body { width: 1200px; height: 900px; overflow: hidden; }
  body {
    background: var(--backdrop);
    font-family: "Lato", sans-serif;
    display: flex;
    flex-direction: column;
    align-items: center;
    justify-content: center;
    gap: 50px;
  }
  .card {
    width: 630px;
    height: 360px;
    border-radius: 18px;
    position: relative;
    box-shadow: 0 6px 18px rgba(0,0,0,0.15);
  }
  .card-back {
    background: var(--brand-blue);
    color: var(--paper);
    display: flex;
    flex-direction: column;
    align-items: center;
    justify-content: center;
  }
  .card-back .wordmark {
    font-weight: 900;
    font-size: 72px;
    letter-spacing: 3px;
  }
  .card-back .web {
    position: absolute;
    bottom: 46px;
    font-size: 15px;
    letter-spacing: 5px;
  }
  .card-front {
    background: var(--paper);
    display: flex;
    align-items: center;
  }
  .front-brand {
    width: 320px;
    display: flex;
    justify-content: center;
    padding-top: 70px;
  }
  .front-brand .wordmark {
    font-weight: 900;
    font-size: 40px;
    letter-spacing: 2px;
    color: var(--brand-blue);
  }
  .divider {
    width: 1.5px;
    height: 150px;
    background: var(--brand-blue);
    margin-top: -10px;
  }
  .contact {
    padding-left: 34px;
    margin-top: -40px;
  }
  .contact .name {
    font-weight: 900;
    font-size: 30px;
    color: var(--brand-blue);
    line-height: 1.1;
  }
  .contact .role {
    font-size: 15px;
    color: var(--ink-grey);
    margin: 2px 0 10px 16px;
  }
  .contact ul { list-style: none; }
  .contact li {
    display: flex;
    align-items: center;
    gap: 10px;
    font-size: 15px;
    color: var(--ink-grey);
    line-height: 24px;
  }
  .contact li svg { width: 15px; height: 15px; fill: var(--brand-blue); flex: none; }
  .contact .accent { color: var(--brand-blue); }
</style>
</head>
<body>
  <section class="card card-back">
    <div class="wordmark">TORVALLE</div>
    <div class="web">www.torvalle.co.uk</div>
  </section>

  <section class="card card-front">
    <div class="front-brand">
      <div class="wordmark">TORVALLE</div>
    </div>
    <div class="divider"></div>
    <div class="contact">
      <div class="name">Martin Ashworth</div>
      <div class="role">CEO</div>
      <ul>
        <li>
          <svg viewBox="0 0 16 16" aria-hidden="true"><path d="M1 5c0-2 3-3 7-3s7 1 7 3v1.5h-3.5V5h-7v1.5H1z"/><rect x="3" y="7" width="10" height="7" rx="1"/></svg>
          0208 5519372
        </li>
        <li>
          <svg viewBox="0 0 16 16" aria-hidden="true"><path d="M4 1h8a1 1 0 0 1 1 1v12a1 1 0 0 1-1 1H4a1 1 0 0 1-1-1V2a1 1 0 0 1 1-1zm0 2v9h8V3z"/></svg>
          +44 7431589027
        </li>
        <li>
          <svg viewBox="0 0 16 16" aria-hidden="true"><path d="M1 3h14v10H1zm1.5 1.5L8 9l5.5-4.5z"/></svg>
          martin@torvalle.co.uk
        </li>
        <li>
          <svg viewBox="0 0 16 16" aria-hidden="true"><path d="M8 1a7 7 0 1 0 0 14A7 7 0 0 0 8 1zm0 1.5c.8 0 1.8 1.6 2 4.5H6c.2-2.9 1.2-4.5 2-4.5zM2.6 7h2c.1-1.8.5-3.2 1-4A5.6 5.6 0 0 0 2.6 7zm8.8 0h2a5.6 5.6 0 0 0-3-4c.5.8.9 2.2 1 4zM2.6 9a5.6 5.6 0 0 0 3 4c-.5-.8-.9-2.2-1-4zm3.4 0c.2 2.9 1.2 4.5 2 4.5s1.8-1.6 2-4.5zm5.4 0c-.1 1.8-.5 3.2-1 4a5.6 5.6 0 0 0 3-4z"/></svg>
          <span>www.<span class="accent">torvalle</span>.co.uk</span>
        </li>
      </ul>
    </div>
  </section>
</body>
</html>
```